Web design required

1-We need a web design for existing company based in New Zealand
2-We build residential house and light commercial
3-We has in-house designer which allow us can provide interior design
4-We modeling project before site construction, which enable both client and construction team to visually analysis whole project,

Target Market(s)

middle class residential house market
Ref: http://www.parvellbuilders.co.nz/

Industry/Entity Type

Construction Company

Number of Pages Required

1 page

Font styles to use
Sans Serif
Other font styles liked:
• Such as : Central Gothic or similar which has more design taste

Colors

Designer to choose colors to be used in the design.

Requirements
Must have
• Front sheet, contact information, sample project

```html
<!DOCTYPE html>
<html lang="en">
<head>
<meta charset="utf-8">
<title>Kestrel Homes</title>
<link href="https://fonts.googleapis.com/css2?family=Questrial&family=Open+Sans:wght@400;600&family=Montserrat:wght@600;700&display=swap" rel="stylesheet">
<style>
:root{
  --blue:#1b6db0;
  --blue-deep:#0f4f8a;
  --ink:#1e1e1e;
  --muted:#6a6a6a;
  --white:#ffffff;
  --dark:#2b2d31;
  --footer:#35373a;
  --field-text:#7a7a7a;
}
*{box-sizing:border-box;margin:0;padding:0}
html,body{width:1200px;height:2748px;overflow:hidden;background:var(--white)}
body{position:relative;font-family:"Open Sans",Arial,sans-serif;color:var(--ink)}
.abs{position:absolute}

/* hero */
.hero-photo{left:0;top:0;width:1200px;height:780px;
  background:linear-gradient(180deg,#3c4350 0%,#4f5054 30%,#5b4a3c 60%,#3a3630 100%)}
.hero-cut{left:0;top:540px}
.brand{left:124px;top:44px;display:flex;align-items:center;gap:14px;color:var(--white);
  font-family:"Questrial",sans-serif;font-size:34px;letter-spacing:5px}
.brand-mark{width:40px;height:40px;border:3px solid var(--white)}
.nav{left:502px;top:46px;display:flex;gap:0;font-family:"Montserrat",sans-serif;font-weight:600;font-size:15px;color:var(--white)}
.nav a{color:inherit;text-decoration:none;display:block;height:40px;line-height:38px;padding:0 34px}
.nav a.current{border:1.5px solid rgba(255,255,255,.85)}
.hero-title{left:0;top:296px;width:1200px;text-align:center;color:var(--white);
  font-family:"Montserrat",sans-serif;font-weight:700;font-size:50px;letter-spacing:5px}
.hero-sub{left:0;top:356px;width:1200px;text-align:center;color:var(--white);
  font-family:"Montserrat",sans-serif;font-weight:600;font-size:36px;letter-spacing:1px}
.slider-dots{left:528px;top:612px;display:flex;gap:6px}
.slider-dots span{width:32px;height:3px;background:rgba(255,255,255,.85)}

/* about */
.about-image{left:551px;top:614px;width:649px;height:558px;
  background:radial-gradient(ellipse at 55% 45%,#dcdcdc 0%,#ececec 45%,#f7f7f7 100%);
  clip-path:polygon(0 49px,100% 0,100% 100%,0 100%)}
.about-title{left:139px;top:764px;font-family:"Questrial",sans-serif;font-size:37px;letter-spacing:1px}
.about-text{left:139px;top:824px;width:370px;font-size:14.5px;line-height:22px;color:var(--muted)}
.about-text p+p{margin-top:22px}
.btn-outline{left:139px;top:1022px;width:167px;height:40px;border:2px solid var(--blue);
  color:var(--blue);font-family:"Montserrat",sans-serif;font-weight:600;font-size:14px;
  text-align:center;line-height:36px}

/* services */
.services{left:0;top:1161px}
.services-title{left:115px;top:1282px;color:var(--white);font-family:"Questrial",sans-serif;font-size:33px;letter-spacing:1px;
  padding-bottom:6px;border-bottom:1.5px solid var(--white)}
.services-text{left:115px;top:1348px;width:440px;color:var(--white);font-size:17px;line-height:25px}
.services-text p+p{margin-top:10px}
.service{color:var(--white)}
.service h3{font-family:"Montserrat",sans-serif;font-weight:700;font-size:20.5px;letter-spacing:.3px}
.service p{font-size:12.5px;line-height:19px;color:#d4d7db;margin-top:6px;width:430px}

/* projects */
.projects-title{left:0;top:1750px;width:1200px;text-align:center;font-family:"Questrial",sans-serif;font-size:32px;letter-spacing:1px}
.projects{left:0;top:1814px}

/* contact */
.contact-bg{left:0;top:2125px;width:1200px;height:550px;
  background:linear-gradient(135deg,#2c2a28 0%,#4a4540 35%,#3b3733 65%,#25241f 100%)}
.contact-notch{left:0;top:2125px}
.contact-title{left:0;top:2224px;width:1200px;text-align:center;color:var(--white);font-family:"Questrial",sans-serif;font-size:32px;letter-spacing:1px}
.field{left:128px;width:443px;height:40px;background:var(--white);color:var(--field-text);font-size:14px;padding:10px 14px}
.field.message{height:106px}
.btn-send{left:128px;top:2574px;width:132px;height:42px;background:var(--blue);color:var(--white);
  font-family:"Montserrat",sans-serif;font-weight:700;font-size:16px;text-align:center;line-height:42px}
.office-title{left:632px;top:2292px;color:#e6e6e6;font-family:"Questrial",sans-serif;font-size:21px}
.office-line{left:630px;display:flex;align-items:center;gap:10px;color:#e6e6e6;font-family:"Questrial",sans-serif;font-size:17px}
.office-line svg{flex:none}
.socials{left:630px;top:2484px;display:flex;gap:8px}
.socials span{width:34px;height:34px;border:1.5px solid #e6e6e6;border-radius:50%}

/* footer */
.footer{left:0;top:2675px;width:1200px;height:73px;background:var(--footer);color:#bdbdbd;
  font-size:13.5px;text-align:center;line-height:73px}
</style>
</head>
<body>

<!-- hero -->
<div class="abs hero-photo" role="img" aria-label="Evening photograph of a two-storey brick house with lit windows, trees and a garage"></div>
<svg class="abs hero-cut" width="1200" height="240" viewBox="0 0 1200 240">
  <polygon points="0,211 1200,19 1200,240 0,240" fill="#ffffff"/>
</svg>
<div class="abs brand"><span class="brand-mark"></span>KESTREL HOMES</div>
<nav class="abs nav">
  <a class="current" href="#">HOME</a>
  <a href="#">ABOUT US</a>
  <a href="#">SERVICES</a>
  <a href="#">PROJECTS</a>
  <a href="#">CONTACT US</a>
</nav>
<h1 class="abs hero-title">WELCOME TO KESTREL HOMES</h1>
<h2 class="abs hero-sub">CONSTRUCTION MODELLING</h2>
<div class="abs slider-dots"><span></span><span></span><span></span><span></span></div>

<!-- about -->
<div class="abs about-image" role="img" aria-label="3D cutaway model of a furnished single-level house floor plan"></div>
<h2 class="abs about-title">ABOUT KESTREL HOMES</h2>
<div class="abs about-text">
  <p>Kestrel Homes is dedicated to creating and renovating beautiful and unusual buildings.</p>
  <p>Kestrel Homes works with you to take dream houses off the blueprints and into reality. We have the knowledge and expertise to customise homes to suit you – from unusual materials and designs to environmentally sensitive locations.</p>
</div>
<div class="abs btn-outline">READ MORE</div>

<!-- services -->
<svg class="abs services" width="1200" height="515" viewBox="0 0 1200 515" role="img" aria-label="Blue tinted house photograph beside darkened photographs of plans, a model and a site meeting">
  <defs>
    <linearGradient id="svcBlue" x1="0" y1="0" x2="1" y2="1">
      <stop offset="0" stop-color="#1f78bd"/>
      <stop offset="1" stop-color="#0d4c86"/>
    </linearGradient>
    <linearGradient id="svcDark1" x1="0" y1="0" x2="1" y2="0">
      <stop offset="0" stop-color="#3a3d42"/>
      <stop offset="1" stop-color="#2a2c30"/>
    </linearGradient>
    <linearGradient id="svcDark2" x1="0" y1="0" x2="1" y2="0">
      <stop offset="0" stop-color="#23262c"/>
      <stop offset="1" stop-color="#30333a"/>
    </linearGradient>
    <linearGradient id="svcDark3" x1="0" y1="0" x2="1" y2="0">
      <stop offset="0" stop-color="#3b4048"/>
      <stop offset="1" stop-color="#2c3036"/>
    </linearGradient>
  </defs>
  <rect width="1200" height="515" fill="url(#svcBlue)"/>
  <polygon points="501,20 1200,20 1200,175 583,175" fill="url(#svcDark1)"/>
  <polygon points="584,178 1200,178 1200,334 666,334" fill="url(#svcDark2)"/>
  <polygon points="668,337 1200,337 1200,493 749,493" fill="url(#svcDark3)"/>
  <!-- icon 1 -->
  <polygon points="489,103 516,56 572,56 599,103 572,150 516,150" fill="#fff" stroke="#1b6db0" stroke-width="5"/>
  <polygon points="522,126 566,82 566,126" fill="none" stroke="#1b6db0" stroke-width="5" stroke-linejoin="round"/>
  <line x1="526" y1="114" x2="550" y2="90" stroke="#1b6db0" stroke-width="4"/>
  <!-- icon 2 -->
  <polygon points="577,259 604,212 660,212 687,259 660,306 604,306" fill="#fff" stroke="#1b6db0" stroke-width="5"/>
  <rect x="608" y="240" width="42" height="36" fill="none" stroke="#1b6db0" stroke-width="4"/>
  <line x1="615" y1="252" x2="635" y2="252" stroke="#1b6db0" stroke-width="3"/>
  <line x1="615" y1="262" x2="630" y2="262" stroke="#1b6db0" stroke-width="3"/>
  <line x1="638" y1="270" x2="662" y2="242" stroke="#1b6db0" stroke-width="5"/>
  <!-- icon 3 -->
  <polygon points="658,415 685,368 741,368 768,415 741,462 685,462" fill="#fff" stroke="#1b6db0" stroke-width="5"/>
  <rect x="692" y="392" width="22" height="46" fill="#1b6db0"/>
  <rect x="716" y="404" width="18" height="34" fill="#1b6db0"/>
  <g fill="#fff">
    <rect x="697" y="398" width="4" height="4"/><rect x="705" y="398" width="4" height="4"/>
    <rect x="697" y="408" width="4" height="4"/><rect x="705" y="408" width="4" height="4"/>
    <rect x="697" y="418" width="4" height="4"/><rect x="705" y="418" width="4" height="4"/>
    <rect x="721" y="412" width="4" height="4"/><rect x="721" y="422" width="4" height="4"/>
  </g>
</svg>
<h2 class="abs services-title">OUR SERVICES</h2>
<div class="abs services-text">
  <p>Vivamus porttitor purus nisi eleifend libero a temp us libero lectus feugiat felis Morbi diam mauris viverra in gravida eu mattis in ante Morbi eget arcu Morbi porta</p>
  <p>libero id ullamcorper nonummy nibh ligula pulvinar metus eget consectetuer augue nisi quis l</p>
</div>
<div class="abs service" style="left:630px;top:1222px">
  <h3>PRECONSTRUCTION PLANNING</h3>
  <p>Cum sociis natoque penatibus et magnis dis parturient montes nascetur ridiculus mus in iaculis</p>
</div>
<div class="abs service" style="left:713px;top:1378px">
  <h3>CONSTRUCTION MODELLING</h3>
  <p>Cum sociis natoque penatibus et magnis dis parturient montes nascetur ridiculus mus in iaculis</p>
</div>
<div class="abs service" style="left:780px;top:1540px">
  <h3>FULL PROJECT MANAGEMENT</h3>
  <p style="width:340px">Cum sociis natoque penatibus et magnis dis parturient montes nascetur ridiculus mus in iaculis facilisis</p>
</div>

<!-- projects -->
<h2 class="abs projects-title">OUR PROJECTS</h2>
<svg class="abs projects" width="1200" height="262" viewBox="0 0 1200 262">
  <defs>
    <linearGradient id="prj1" x1="0" y1="0" x2="1" y2="1"><stop offset="0" stop-color="#3b3d42"/><stop offset=".5" stop-color="#d9d9d7"/><stop offset="1" stop-color="#6a6258"/></linearGradient>
    <linearGradient id="prj2" x1="0" y1="0" x2="0" y2="1"><stop offset="0" stop-color="#3e6fb6"/><stop offset=".55" stop-color="#c8c6c0"/><stop offset="1" stop-color="#8d8a84"/></linearGradient>
    <linearGradient id="prj3" x1="0" y1="0" x2="0" y2="1"><stop offset="0" stop-color="#2f7bc0"/><stop offset="1" stop-color="#1a5d9c"/></linearGradient>
    <linearGradient id="prj4" x1="0" y1="0" x2="1" y2="1"><stop offset="0" stop-color="#f2f2f2"/><stop offset=".45" stop-color="#b07a4e"/><stop offset="1" stop-color="#ece9e5"/></linearGradient>
  </defs>
  <g role="img" aria-label="Photograph of a white weatherboard house entrance with letterbox">
    <polygon points="245,0 358,65 358,197 245,262 132,197 132,65" fill="url(#prj1)"/>
  </g>
  <g role="img" aria-label="Photograph of a modern two-storey house at dusk">
    <polygon points="484,0 597,65 597,197 484,262 371,197 371,65" fill="url(#prj2)"/>
  </g>
  <g role="img" aria-label="Blue tinted photograph of a house under construction">
    <polygon points="722,0 835,65 835,197 722,262 609,197 609,65" fill="url(#prj3)"/>
  </g>
  <text x="722" y="127" text-anchor="middle" fill="#fff" font-family="Montserrat, sans-serif" font-weight="700" font-size="18">ASHFORD</text>
  <text x="722" y="150" text-anchor="middle" fill="#fff" font-family="Montserrat, sans-serif" font-weight="700" font-size="18">PROJECT</text>
  <g role="img" aria-label="Photograph of timber ceiling and interior detailing">
    <polygon points="960,0 1073,65 1073,197 960,262 847,197 847,65" fill="url(#prj4)"/>
  </g>
</svg>

<!-- contact -->
<div class="abs contact-bg" role="img" aria-label="Dimmed photograph of a modern kitchen interior"></div>
<svg class="abs contact-notch" width="1200" height="70" viewBox="0 0 1200 70">
  <polygon points="421,0 600,62 788,0" fill="#ffffff"/>
  <polyline points="421,0 600,64 788,0" fill="none" stroke="#cfcfcf" stroke-width="2"/>
</svg>
<h2 class="abs contact-title">CONTACT US</h2>
<div class="abs field" style="top:2301px">Name</div>
<div class="abs field" style="top:2352px">Email</div>
<div class="abs field" style="top:2404px">Phone</div>
<div class="abs field message" style="top:2455px">Message</div>
<div class="abs btn-send">SEND</div>

<div class="abs office-title">Head Office</div>
<div class="abs office-line" style="top:2341px">
  <svg width="34" height="34" viewBox="0 0 34 34"><circle cx="17" cy="17" r="15.5" fill="none" stroke="#e6e6e6" stroke-width="1.5"/><path d="M17 9a6 6 0 0 0-6 6c0 5 6 11 6 11s6-6 6-11a6 6 0 0 0-6-6z" fill="none" stroke="#e6e6e6" stroke-width="1.8"/><circle cx="17" cy="15" r="2" fill="#e6e6e6"/></svg>
  27 Harbourview Lane, Eastgate Auckland
</div>
<div class="abs office-line" style="top:2383px">
  <svg width="34" height="34" viewBox="0 0 34 34"><circle cx="17" cy="17" r="15.5" fill="none" stroke="#e6e6e6" stroke-width="1.5"/><path d="M11 10l4 0 1.5 4-2 1.5c1 2 2.5 3.5 4.5 4.5l1.5-2 4 1.5v4c-8 1-14-5-13.5-13.5z" fill="none" stroke="#e6e6e6" stroke-width="1.6" stroke-linejoin="round"/></svg>
  info@kestrelhomes.co.nz
</div>
<div class="abs office-line" style="top:2424px">
  <svg width="34" height="34" viewBox="0 0 34 34"><circle cx="17" cy="17" r="15.5" fill="none" stroke="#e6e6e6" stroke-width="1.5"/><rect x="10" y="12" width="14" height="10" fill="none" stroke="#e6e6e6" stroke-width="1.6"/><polyline points="10,12 17,18 24,12" fill="none" stroke="#e6e6e6" stroke-width="1.6"/></svg>
  Tel: 0064 9 000 4821
</div>
<div class="abs socials"><span></span><span></span><span></span><span></span></div>

<footer class="abs footer">© 2017 Company Name&nbsp; All right reserved&nbsp; Term of Use</footer>

</body>
</html>
```